Road Construction Company needs business cards

We would like a new business card designed for our business.

We're a road construction company based in Qld, Australia.

Can the business card please have the following information on it.

Name: Warren Halbeck
Position: General Manager
Phone: 0472 915 348
Email: Warren.halbeck@tovrin.com.au
Address: 87 Marrow Ave, Pendlebay, QLD, 4023
Website: www.tovrin.com.au

Visually we'd like the card to be professional and simple.

Attached is our logo.

Our website is www.tovrin.com.au

Target Market(s)

Men aged 25-60

Contact Information for Business Card

As listed in project description

Font styles to use
Serif

Requirements
Must have
• Large logo on back of card

```html
<!DOCTYPE html>
<html lang="en">
<head>
<meta charset="utf-8">
<title>Tovrin Business Card</title>
<link rel="stylesheet" href="https://fonts.googleapis.com/css2?family=Exo+2:wght@400;600;700;800&display=swap">
<style>
  :root {
    --page-bg: #1b1b1c;
    --card-bg: #0f0f10;
    --accent: #2fa3d8;
    --logo-blue: #1768c4;
    --text-light: #f2f2f2;
    --divider: #8a8a8a;
  }
  * { box-sizing: border-box; margin: 0; padding: 0; }
  html, body { width: 1200px; height: 900px; overflow: hidden; }
  body {
    background: var(--page-bg);
    font-family: "Exo 2", sans-serif;
    color: var(--text-light);
    position: relative;
  }
  .card {
    position: absolute;
    left: 320px;
    width: 560px;
    height: 320px;
    background: var(--card-bg);
    box-shadow: 0 10px 30px rgba(0,0,0,0.6);
    overflow: hidden;
  }
  .card::after {
    content: "";
    position: absolute;
    left: 0; right: 0; bottom: 0;
    height: 12px;
    background: var(--accent);
  }
  .card-front { top: 100px; }
  .card-back { top: 460px; }

  .brand {
    position: absolute;
    inset: 0 0 12px 0;
    display: flex;
    align-items: center;
    justify-content: center;
  }
  .brand-name {
    font-family: "Exo 2", sans-serif;
    font-weight: 800;
    font-size: 64px;
    letter-spacing: 4px;
    text-transform: uppercase;
    color: var(--logo-blue);
  }

  .identity {
    position: absolute;
    right: 298px;
    top: 96px;
    text-align: right;
  }
  .person-name {
    font-family: "Exo 2", sans-serif;
    font-weight: 800;
    font-size: 22px;
    line-height: 26px;
    color: var(--accent);
    text-transform: uppercase;
    white-space: nowrap;
    letter-spacing: 1px;
  }
  .person-role {
    margin-top: 2px;
    font-size: 16px;
    color: var(--text-light);
  }
  .divider {
    position: absolute;
    left: 276px;
    top: 122px;
    width: 1px;
    height: 62px;
    background: var(--divider);
  }
  .contact-list {
    position: absolute;
    left: 290px;
    top: 122px;
    list-style: none;
  }
  .contact-list li {
    display: flex;
    align-items: center;
    gap: 8px;
    font-size: 15px;
    line-height: 21px;
    white-space: nowrap;
  }
  .contact-list svg { width: 13px; height: 13px; flex: none; }
  .address {
    position: absolute;
    left: 110px;
    bottom: 48px;
    font-size: 16px;
    letter-spacing: 0.3px;
  }
</style>
</head>
<body>

  <section class="card card-front">
    <div class="brand">
      <span class="brand-name">Tovrin</span>
    </div>
  </section>

  <section class="card card-back">
    <div class="identity">
      <p class="person-name">Warren Halbeck</p>
      <p class="person-role">General Manager</p>
    </div>
    <div class="divider"></div>
    <ul class="contact-list">
      <li>
        <svg viewBox="0 0 16 16" aria-hidden="true"><path fill="#2fa3d8" d="M3.6 1.2l2.3 2.6-1.3 1.7c.8 1.9 2.2 3.3 4.1 4.1l1.7-1.3 2.6 2.3-1.3 2.5C6.5 13.2 2.8 9.5 1.1 4.3z"/></svg>
        <span>0472 915 348</span>
      </li>
      <li>
        <svg viewBox="0 0 16 16" aria-hidden="true"><rect x="1" y="3" width="14" height="10" fill="#2fa3d8"/><path d="M1 3l7 6 7-6" fill="none" stroke="#0f0f10" stroke-width="1.4"/></svg>
        <span>Warren.halbeck@tovrin.com.au</span>
      </li>
      <li>
        <svg viewBox="0 0 16 16" aria-hidden="true"><g fill="none" stroke="#2fa3d8" stroke-width="1.4"><circle cx="8" cy="8" r="6.5"/><ellipse cx="8" cy="8" rx="3" ry="6.5"/><path d="M1.5 8h13M2.5 4.8h11M2.5 11.2h11"/></g></svg>
        <span>www.tovrin.com.au</span>
      </li>
    </ul>
    <p class="address">87 Marrow Ave, Pendlebay, QLD, 4023</p>
  </section>

</body>
</html>
```